Brell Stone Company Business Cards

Front and Back Business Card - logo and text setup - cool design. I need workable photoshop or illustrator files so I can setup each employee card with design that is created
Updates

Hi everyone, thank you for the great entries. Please no more white and blue cards - there are so many already - black and silver only now please. thanks!

Target Market(s)

Construction Industry - Facility Managers

Industry/Entity Type

Construction

Contact Information for Business Card

I really like contemporary simplistic looks - clean neat....not opposed to seeing some black backrounds

Requirements
Must have
• Logo/website address with design on front only - www.brellstone-example.com (logo attached)
• Back:
• Name/Title/Company Address/Phone/email address
Nice to have
• Cool design
Should not have
• Nothing gimmicky like Fire or Water - since we are a Fire Protection company - it has all been done

```html
<!DOCTYPE html>
<html lang="en">
<head>
<meta charset="utf-8">
<title>Brell Stone Company Business Cards</title>
<link rel="stylesheet" href="https://fonts.googleapis.com/css2?family=Open+Sans:wght@400;700;800&display=swap">
<style>
  :root {
    --page: #1c1c1e;
    --card: #050505;
    --brand-blue: #0a2899;
    --brand-red: #ff2222;
    --brand-coral: #ff5a45;
    --text-light: #ffffff;
    --text-muted: #d8d8d8;
  }
  * { box-sizing: border-box; margin: 0; padding: 0; }
  html, body {
    width: 1200px; height: 960px; overflow: hidden;
    background: var(--page);
    font-family: "Open Sans", Arial, sans-serif;
  }
  .canvas {
    position: relative; width: 1200px; height: 960px;
  }
  .card {
    position: absolute; left: 250px; width: 700px; height: 400px;
    background: var(--card); overflow: hidden;
  }
  .card--front { top: 60px; }
  .card--back { top: 500px; }

  .brand {
    display: flex; align-items: center; gap: 14px;
    color: var(--brand-blue); font-weight: 800; letter-spacing: -0.5px;
    white-space: nowrap;
  }
  .brand__square {
    width: 22px; height: 22px; background: var(--brand-red); flex: none;
  }
  .card--front .brand {
    position: absolute; top: 140px; left: 0; right: 0;
    justify-content: center; font-size: 50px;
  }
  .front__web {
    position: absolute; top: 240px; left: 0; right: 0; text-align: center;
    color: var(--text-muted); font-size: 17px; letter-spacing: 3px;
  }

  .card--back .brand {
    position: absolute; top: 48px; left: 40px; font-size: 40px;
  }
  .back__shapes { position: absolute; inset: 0; }
  .contact {
    position: absolute; left: 40px; top: 226px;
    list-style: none; color: var(--text-light); font-size: 15px; line-height: 27px;
  }
  .contact__item { display: flex; align-items: center; gap: 10px; }
  .contact__icon { width: 14px; height: 14px; flex: none; }
  .person {
    position: absolute; right: 24px; top: 300px; text-align: right;
    color: var(--text-light); font-size: 15px; line-height: 21px;
  }
  .person__name { font-weight: 700; font-size: 19px; line-height: 24px; }
</style>
</head>
<body>
<main class="canvas">
  <section class="card card--front" aria-label="Card front">
    <div class="brand"><span class="brand__square"></span>Brell Stone Company</div>
    <p class="front__web">www.brellstone-example.com</p>
  </section>

  <section class="card card--back" aria-label="Card back">
    <svg class="back__shapes" width="700" height="400" viewBox="0 0 700 400" aria-hidden="true">
      <polygon points="0,212 470,212 270,322 0,322" fill="var(--brand-blue)"/>
      <polygon points="275,332 398,300 452,400 330,400" fill="var(--brand-coral)"/>
      <polygon points="385,222 700,296 700,400 478,400" fill="var(--brand-red)"/>
    </svg>
    <div class="brand"><span class="brand__square"></span>Brell Stone Company</div>
    <ul class="contact">
      <li class="contact__item">
        <svg class="contact__icon" viewBox="0 0 16 16" aria-hidden="true"><path d="M4 1l3 3-2 2c1 2 3 4 5 5l2-2 3 3-2 3C7 15 1 9 1 3z" fill="#fff"/></svg>
        (555) 014-2290
      </li>
      <li class="contact__item">
        <svg class="contact__icon" viewBox="0 0 16 16" aria-hidden="true"><rect x="1" y="3" width="14" height="10" fill="#fff"/><path d="M1 3l7 6 7-6" stroke="#0a2899" stroke-width="1.5" fill="none"/></svg>
        info@brellstone-example.com
      </li>
      <li class="contact__item">
        <svg class="contact__icon" viewBox="0 0 16 16" aria-hidden="true"><circle cx="8" cy="8" r="6.5" stroke="#fff" stroke-width="1.5" fill="none"/><path d="M1.5 8h13M8 1.5c-3 3-3 10 0 13M8 1.5c3 3 3 10 0 13" stroke="#fff" stroke-width="1.2" fill="none"/></svg>
        www.brellstone-example.com
      </li>
    </ul>
    <div class="person">
      <p class="person__name">Dana Whitfield</p>
      <p class="person__title">President</p>
      <p class="person__address">48 Harbor Point Road</p>
      <p class="person__address">Millbrook, NY 10099</p>
    </div>
  </section>
</main>
</body>
</html>
```